Torvadex needs a website to buy and sell phones and electronics

We need a website to buy and sell smartphones.
https://www.quicklorratrade.com/
http://www.bramblequayshop.co.uk/
http://tradeyourunit.halvestorndepot.com/
https://www.k9loopbacker.co.uk/
https://www.brolvenmartex.co.uk/we-buy/

I logged into plorna.com and went to their online store template. I iike their template on the camera shop. I like the big letters but with elegance and formality. See link below:
http://www.plorna.com/website-template/view/html/1625?originUrl=http%3A%2F%2Fwww.plorna.com%2Fwebsite%2Ftemplates%2Fhtml%2Fonline-store%2F2&bookName=&galleryDocIndex=0&category=online-store

We know that these websites are too much work but we only need the landing page, without the that big search box. We want the various qavrixes such Qavrixes 4, 5, 6 and 7 and Turnwell Orbit S3, S4, S5 and S6 be listed with corresponding prices in Philippine currency.

We don't have a logo yet.

Notes To Designers: I would like to have a good feel of the site and I hope these sites can give you a feel. - quicklorratrade.com - bramblequayshop.co.uk Note: Please read the brief for updates. Also: i paid for the coded website so I believe it must be a running website. Thank you.

Target Market(s)

Philippines

Industry/Entity Type

Electronics

Coding

Coded - Design and coding required

Number of Pages Required

5+ page

Requirements
Must have
• Must displays phones of Qavrixes and Turnwell (Only the latest models for the last 2-3 years) not old
• Lumtabs and Kordial as well
Nice to have
• Logo - we need logo
• I love the simplicity but elegance of https://www.quicklorratrade.com/

```html
<!DOCTYPE html>
<html lang="en">
<head>
<meta charset="utf-8">
<title>Torvadex – Buy &amp; Sell Smartphones</title>
<link rel="stylesheet" href="https://fonts.googleapis.com/css2?family=Mulish:wght@300;400;600;700&family=Open+Sans:ital,wght@0,400;0,600;1,400&display=swap">
<style>
:root{
  --navy:#0a4a8c;
  --hero-top:#0b4f9a;
  --hero-bottom:#13b6e8;
  --brand-blue:#1a5aa0;
  --sky:#1ba2d8;
  --text-grey:#666;
  --muted:#999;
  --panel:#f1f1f1;
  --footer:#ececec;
  --line:#d9d9d9;
  --star:#f5a623;
  --white:#fff;
}
*{margin:0;padding:0;box-sizing:border-box}
html,body{width:707px;height:1200px;overflow:hidden;background:var(--white)}
body{position:relative;font-family:"Mulish",sans-serif;color:var(--text-grey)}
.abs{position:absolute}
.center{text-align:center}

/* header + hero */
.hero{left:0;top:0;width:707px;height:360px;overflow:hidden;background:linear-gradient(160deg,var(--hero-top) 0%,#0e7cc6 55%,var(--hero-bottom) 100%)}
.topbar{left:0;top:0;width:707px;height:65px;background:rgba(10,60,130,.55)}
.logo{left:72px;top:17px;font-size:26px;font-weight:600;color:var(--white);letter-spacing:.2px}
.nav{top:27px;font-size:12px;color:var(--white)}
.hero-kicker{left:0;width:707px;top:84px;font-size:18.5px;font-weight:300;color:var(--white);letter-spacing:.4px}
.hero-title{left:0;width:707px;top:104px;font-size:27.5px;font-weight:700;color:var(--white)}
.btn{top:143px;height:21px;border:1.5px solid var(--white);color:var(--white);font-size:9px;line-height:18px;text-align:center}

.phone-back{left:328px;top:181px;width:114px;height:179px;border-radius:16px 16px 0 0;background:#f3f4f5;border:3px solid #dfe3e6;border-bottom:none}
.phone-back-screen{left:342px;top:206px;width:92px;height:154px;background:linear-gradient(170deg,#1f3b3a,#2e6f66 60%,#9fc9cf)}
.phone-front{left:250px;top:202px;width:93px;height:158px;border-radius:14px 14px 0 0;background:linear-gradient(180deg,#d6d0c2,#b9b3a6);border:2px solid #c9c2b2;border-bottom:none}
.phone-front-screen{left:256px;top:224px;width:81px;height:136px;background:linear-gradient(160deg,#3a3552,#8a6d8f 55%,#d7b6a4)}
.cash-photo{left:471px;top:276px;width:143px;height:84px;border-radius:6px 40px 0 0;background:linear-gradient(110deg,#b8d3e2 0%,#d7e3ea 55%,#e7c2a0 100%)}

/* how it works */
.section-title{left:0;width:707px;font-size:19px;font-weight:400;color:var(--brand-blue)}
.step-line{left:175px;top:449px;width:354px;height:1px;background:var(--brand-blue)}
.step-circle{top:417px;width:66px;height:66px;border-radius:50%;border:1.5px solid var(--brand-blue);background:var(--white)}
.step-circle svg{position:absolute;left:16px;top:16px}
.step-title{top:491px;width:170px;font-size:13.5px;line-height:15.5px;color:#666;letter-spacing:.3px}
.step-text{top:530px;width:170px;font-family:"Open Sans",sans-serif;font-size:7.5px;line-height:12.5px;color:var(--muted)}

/* deals */
.deals{left:0;top:592px;width:707px;height:276px;background:var(--panel);border-top:1px solid var(--line);border-bottom:1px solid var(--line)}
.deals-title{left:0;width:707px;top:617px;font-size:17px;color:#444}
.rule{top:630px;width:30px;height:1px;background:#aaa}
.dot{top:628px;width:5px;height:5px;border-radius:50%;background:#aaa}
.device{width:52px;border-radius:8px}
.device-name{top:782px;width:110px;font-size:10.5px;color:var(--brand-blue)}
.device-text{top:797px;width:110px;font-family:"Open Sans",sans-serif;font-size:7px;line-height:10.5px;color:var(--muted)}
.device-price{top:818px;width:110px;font-size:14px;color:var(--sky)}

/* reviews */
.reviews-title{left:0;width:707px;top:895px;font-size:18px;color:var(--sky);letter-spacing:.3px}
.review{top:932px;width:183px;height:96px;border:1px solid #e4e4e4;background:var(--white)}
.review-text{top:946px;width:150px;font-family:"Open Sans",sans-serif;font-style:italic;font-size:7.5px;line-height:13.5px;color:#555}
.avatar{top:1004px;width:42px;height:42px;border-radius:50%;border:2px solid var(--white);background:linear-gradient(160deg,#e8d6c4,#a77a5c)}
.author{top:1046px;width:120px;font-family:"Open Sans",sans-serif;font-weight:600;font-size:8px;color:#333}
.stars{top:1058px;width:120px;font-size:12px;color:var(--star);letter-spacing:1px}

/* footer */
.footer{left:0;top:1123px;width:707px;height:77px;background:var(--footer)}
.foot-link{top:1147px;font-size:9.5px;color:#555}
.copyright{left:81px;top:1170px;font-size:7px;color:#888}
.social{top:1149px;width:21px;height:21px;border-radius:50%;background:var(--white)}
.social svg{position:absolute;left:5px;top:5px}
</style>
</head>
<body>

<div class="abs hero"></div>
<div class="abs topbar"></div>
<div class="abs logo">Torvadex</div>
<div class="abs nav" style="left:295px">About</div>
<div class="abs nav" style="left:349px">How it Works</div>
<div class="abs nav" style="left:441px">Sell or Buy</div>
<div class="abs nav" style="left:519px">Support</div>
<div class="abs nav" style="left:584px">Contact</div>

<div class="abs hero-kicker center">BUY &amp; SELL SMARTPHONES</div>
<div class="abs hero-title center">GET A BEST PRICE NOW</div>
<div class="abs btn" style="left:272px;width:82px">Want to Sell</div>
<div class="abs btn" style="left:357px;width:78px">Want to Buy</div>

<svg class="abs" style="left:71px;top:185px" width="14" height="22" viewBox="0 0 14 22"><path d="M11 2 3 11l8 9" fill="none" stroke="#fff" stroke-width="2.5"/></svg>
<svg class="abs" style="left:627px;top:185px" width="14" height="22" viewBox="0 0 14 22"><path d="M3 2l8 9-8 9" fill="none" stroke="#fff" stroke-width="2.5"/></svg>

<div role="img" aria-label="Two smartphones standing side by side">
  <div class="abs phone-back"></div>
  <div class="abs phone-back-screen"></div>
  <div class="abs phone-front"></div>
  <div class="abs phone-front-screen"></div>
</div>
<div class="abs cash-photo" role="img" aria-label="Hand holding peso banknotes"></div>

<!-- How it works -->
<div class="abs section-title center" style="top:380px">How it Works</div>
<div class="abs step-line"></div>

<div class="abs step-circle" style="left:142px">
  <svg width="32" height="32" viewBox="0 0 32 32" fill="none" stroke="#1a5aa0" stroke-width="2"><path d="M2 5h5l4 15h15l3-11H9"/><path d="M12 12h14M13 16h12"/><circle cx="13" cy="26" r="2"/><circle cx="23" cy="26" r="2"/></svg>
</div>
<div class="abs step-circle" style="left:319px">
  <svg width="32" height="32" viewBox="0 0 32 32" fill="none" stroke="#1a5aa0" stroke-width="2"><path d="M20 28H5V3h13l5 5v8"/><path d="M9 19h9M9 23h7"/><path d="M11 9a3 3 0 1 1 3 3v2"/><circle cx="24" cy="24" r="5" fill="#1a5aa0"/><path d="M24 21v6M21 24h6" stroke="#fff"/></svg>
</div>
<div class="abs step-circle" style="left:496px">
  <svg width="32" height="32" viewBox="0 0 32 32" fill="none" stroke="#1a5aa0" stroke-width="2"><path d="M9 3h18v20l-6 6H9"/><path d="M15 9v10M15 9h4a3 3 0 0 1 0 6h-4M13 12h9"/><path d="M3 22l4 4 6-7"/></svg>
</div>

<div class="abs step-title center" style="left:90px">Get a Quote and<br>Place Order</div>
<div class="abs step-title center" style="left:269px">Well' Check your Device<br>and Confirm Quote</div>
<div class="abs step-title center" style="left:444px">Get Paid on the<br>Same Day</div>
<div class="abs step-text center" style="left:88px">sociosqu ad litora torquent per conubia<br>nostra per inceptos hymena</div>
<div class="abs step-text center" style="left:267px">sociosqu ad litora torquent per conubia<br>nostra per inceptos hymena</div>
<div class="abs step-text center" style="left:444px">sociosqu ad litora torquent per conubia<br>nostra per inceptos hymena</div>

<!-- Deals -->
<div class="abs deals"></div>
<div class="abs deals-title center">Most Recent Devices Deals</div>
<div class="abs rule" style="left:203px"></div><div class="abs dot" style="left:229px"></div>
<div class="abs dot" style="left:471px"></div><div class="abs rule" style="left:473px"></div>

<svg class="abs" style="left:63px;top:705px" width="14" height="36" viewBox="0 0 14 36"><path d="M12 1 2 18l10 17" fill="none" stroke="#bbb" stroke-width="1"/></svg>
<svg class="abs" style="left:635px;top:705px" width="14" height="36" viewBox="0 0 14 36"><path d="M2 1l10 17-10 17" fill="none" stroke="#bbb" stroke-width="1"/></svg>

<div class="abs device" style="left:101px;top:676px;height:95px;background:linear-gradient(160deg,#2b3f6e,#8aa4c8)" role="img" aria-label="Orbit S3 phone"></div>
<div class="abs device" style="left:218px;top:670px;height:102px;width:49px;background:linear-gradient(160deg,#111,#4a4a4a)" role="img" aria-label="Qavrix 5 phone"></div>
<div class="abs device" style="left:329px;top:665px;height:108px;background:linear-gradient(160deg,#111,#3a6aa8)" role="img" aria-label="Qavrix 6 phone"></div>
<div class="abs device" style="left:440px;top:666px;height:108px;background:linear-gradient(160deg,#eee,#3c8a6a)" role="img" aria-label="Qavrix 7 phone"></div>
<div class="abs device" style="left:550px;top:670px;height:104px;background:linear-gradient(160deg,#ddd,#e24a8a 50%,#3fb6e0)" role="img" aria-label="Orbit S6 phone"></div>

<div class="abs device-name center" style="left:75px">Orbit S3</div>
<div class="abs device-name center" style="left:188px">qavrix5</div>
<div class="abs device-name center" style="left:301px">qavrix6</div>
<div class="abs device-name center" style="left:413px">qavrix7</div>
<div class="abs device-name center" style="left:525px">Orbit S6</div>

<div class="abs device-text center" style="left:75px">sociosqu ad litora torquent<br>per conubia nostra</div>
<div class="abs device-text center" style="left:188px">sociosqu ad litora torquent<br>per conubia nostra</div>
<div class="abs device-text center" style="left:301px">sociosqu ad litora torquent<br>per conubia nostra</div>
<div class="abs device-text center" style="left:413px">sociosqu ad litora torquent<br>per conubia nostra</div>
<div class="abs device-text center" style="left:525px">sociosqu ad litora torquent<br>per conubia nostra</div>

<div class="abs device-price center" style="left:75px">₱40</div>
<div class="abs device-price center" style="left:188px">₱35</div>
<div class="abs device-price center" style="left:301px">₱ 50</div>
<div class="abs device-price center" style="left:413px">₱75</div>
<div class="abs device-price center" style="left:525px">₱70</div>

<!-- Reviews -->
<div class="abs reviews-title center">Customer Reviews</div>
<div class="abs review" style="left:72px"></div>
<div class="abs review" style="left:263px"></div>
<div class="abs review" style="left:454px"></div>

<div class="abs review-text center" style="left:88px;top:950px">Morbi diam mauris viverra in gravida eu mattis in ante Morbi eget arcu Morbi porta libero id ullamcorper nonummy nibh</div>
<div class="abs review-text center" style="left:279px;top:950px">Sociosqu ad litora torquent per conubia nostra per inceptos hymenaeos Proin nulla arcu nonummy luctus dictum eget</div>
<div class="abs review-text center" style="left:470px;top:943px">Praesent sit amet est In dictum dolor eu dictum porttitor enim felis viverra mi eget luctus massa purus quis odio Etiam nulla massa pharetra facilisis</div>

<div class="abs avatar" style="left:143px" role="img" aria-label="Customer portrait"></div>
<div class="abs avatar" style="left:333px;background:linear-gradient(160deg,#7fd0d8,#6b4a38)" role="img" aria-label="Customer portrait"></div>
<div class="abs avatar" style="left:524px;background:linear-gradient(160deg,#e6eef3,#d8b08a)" role="img" aria-label="Customer portrait"></div>

<div class="abs author center" style="left:103px">By Author Name</div>
<div class="abs author center" style="left:294px">By Author Name</div>
<div class="abs author center" style="left:485px">By Author Name</div>
<div class="abs stars center" style="left:103px">★★★★</div>
<div class="abs stars center" style="left:294px">★★★★</div>
<div class="abs stars center" style="left:484px">★★★★</div>

<!-- Footer -->
<div class="abs footer"></div>
<div class="abs foot-link" style="left:81px">Home</div>
<div class="abs foot-link" style="left:125px">About</div>
<div class="abs foot-link" style="left:170px">How it Works</div>
<div class="abs foot-link" style="left:246px">Sell or Buy</div>
<div class="abs foot-link" style="left:311px">Support</div>
<div class="abs foot-link" style="left:364px">Contact</div>
<div class="abs copyright">© 2017 Company Name &nbsp;All right reserved &nbsp;Term of Use</div>

<div class="abs social" style="left:529px" aria-label="Social link"><svg width="11" height="11" viewBox="0 0 11 11"><circle cx="5.5" cy="5.5" r="3.5" fill="none" stroke="#1a8ad8" stroke-width="1.6"/></svg></div>
<div class="abs social" style="left:556px" aria-label="Social link"><svg width="11" height="11" viewBox="0 0 11 11"><circle cx="5.5" cy="5.5" r="3.5" fill="none" stroke="#1a8ad8" stroke-width="1.6"/></svg></div>
<div class="abs social" style="left:584px" aria-label="Social link"><svg width="11" height="11" viewBox="0 0 11 11"><circle cx="5.5" cy="5.5" r="3.5" fill="none" stroke="#1a8ad8" stroke-width="1.6"/></svg></div>
<div class="abs social" style="left:611px" aria-label="Social link"><svg width="11" height="11" viewBox="0 0 11 11"><circle cx="5.5" cy="5.5" r="3.5" fill="none" stroke="#1a8ad8" stroke-width="1.6"/></svg></div>

</body>
</html>
```